A Modern & Sleek "Coming Soon" Page for an A.I Recruiting App

For the “Coming Soon” website, a simple background with no people in it. I've attached an A.I image of what the page should generally look like.

- A single mobile phone as the main focus where the user actually clicks on the, “notify me” button (after entering their email address).
- In the background where the pillars/columns are seen in the example, should be subtle pad locks that are in their opened position with a key inside the lock. I've attached images to try to illustrate this idea, but they are far away in style from what I'm looking for.

SLOGAN: Unlocking the power of meaningful connections
LOGO/TITLE: Should be the name as shown in image with only the name "KelvoLink" on it
COLORS: Purplish/blue hues. Should not be too feminine
NOTE: The user should only click once when signing up/entering their email.

Product: A recruiting platform that matches employers/employees with A.I. and prioritizing cultural fit/values system before skills. The industry we are tackling first is the caregiving industry (nannies, tutors, elderly). All users will be background screened and that info lives on the blockchain. All users will have the option to review and be reviewed/rated.

```html
<!DOCTYPE html>
<html lang="en">
<head>
<meta charset="UTF-8">
<title>KelvoLink — Coming Soon</title>
<link rel="stylesheet" href="https://fonts.googleapis.com/css2?family=EB+Garamond:wght@500&family=Montserrat:wght@200;600;700&display=swap">
<style>
  :root {
    --bg-deep: #07131f;
    --bg-mid: #122c42;
    --bg-glow: #1f4a68;
    --lock-tone: #2b5470;
    --lock-light: #5d8aa6;
    --ink-white: #ffffff;
    --screen-top: #5f86a8;
    --screen-bottom: #3f6f98;
    --phone-body: #0c0f14;
    --field: #9fb6cb;
    --button: #4a22a0;
  }
  * { margin: 0; padding: 0; box-sizing: border-box; }
  html, body { width: 1200px; height: 667px; overflow: hidden; background: var(--bg-deep); }
  .canvas {
    position: relative;
    width: 1200px;
    height: 667px;
    overflow: hidden;
    background:
      radial-gradient(ellipse at 70% 45%, var(--bg-glow) 0%, transparent 55%),
      linear-gradient(160deg, var(--bg-mid) 0%, var(--bg-deep) 70%);
  }
  .hero-art {
    position: absolute;
    left: 390px;
    top: 100px;
    width: 720px;
    height: 470px;
    border-radius: 40px;
    background: radial-gradient(ellipse at 55% 55%, var(--lock-light) 0%, var(--lock-tone) 35%, transparent 72%);
    opacity: 0.55;
  }
  .brand {
    position: absolute;
    top: 40px;
    left: 0;
    width: 100%;
    text-align: center;
    font-family: "Montserrat", sans-serif;
    font-weight: 200;
    font-size: 58px;
    letter-spacing: 8px;
    color: var(--ink-white);
    text-transform: uppercase;
  }
  .slogan {
    position: absolute;
    left: 588px;
    top: 252px;
    font-family: "EB Garamond", serif;
    font-weight: 500;
    font-size: 36px;
    line-height: 75px;
    color: var(--ink-white);
    text-transform: uppercase;
  }
  .phone {
    position: absolute;
    left: 150px;
    top: 150px;
    width: 275px;
    height: 490px;
    border-radius: 40px;
    background: var(--phone-body);
    padding: 12px;
    transform: rotate(-6deg);
    box-shadow: 0 20px 40px rgba(0,0,0,0.55);
  }
  .phone-screen {
    position: relative;
    width: 100%;
    height: 100%;
    border-radius: 30px;
    background: linear-gradient(180deg, var(--screen-top), var(--screen-bottom));
    overflow: hidden;
    text-align: center;
    font-family: "Montserrat", sans-serif;
    color: var(--ink-white);
  }
  .phone-notch {
    position: absolute;
    top: 0;
    left: 50%;
    width: 120px;
    height: 22px;
    margin-left: -60px;
    border-radius: 0 0 14px 14px;
    background: var(--phone-body);
  }
  .screen-brand {
    margin-top: 100px;
    font-weight: 600;
    font-size: 20px;
    letter-spacing: 1px;
    text-transform: uppercase;
  }
  .screen-slogan {
    margin-top: 20px;
    font-weight: 600;
    font-size: 15px;
    line-height: 34px;
    text-transform: uppercase;
  }
  .email-field {
    display: block;
    width: 150px;
    height: 44px;
    margin: 40px auto 0;
    border: none;
    border-radius: 22px;
    background: var(--field);
    color: var(--ink-white);
    font-family: "Montserrat", sans-serif;
    font-size: 10px;
    font-weight: 600;
    padding-left: 14px;
    text-transform: uppercase;
  }
  .email-field::placeholder { color: var(--ink-white); }
  .notify-button {
    display: block;
    width: 160px;
    height: 52px;
    margin: 16px auto 0;
    border: none;
    border-radius: 26px;
    background: var(--button);
    color: var(--ink-white);
    font-family: "Montserrat", sans-serif;
    font-weight: 700;
    font-size: 15px;
    text-transform: uppercase;
  }
</style>
</head>
<body>
  <main class="canvas">
    <div class="hero-art" role="img" aria-label="Open padlock with a key in its lock, set on a circuit and binary code background"></div>

    <h1 class="brand">KelvoLink</h1>

    <p class="slogan">Unlocking the power<br>of meaningful<br>connections</p>

    <div class="phone">
      <div class="phone-screen">
        <div class="phone-notch"></div>
        <p class="screen-brand">KelvoLink</p>
        <p class="screen-slogan">Unlocking the power<br>of meaningful<br>connections</p>
        <input class="email-field" type="email" placeholder="Enter email here" aria-label="Email address">
        <button class="notify-button" type="button">Notify me</button>
      </div>
    </div>
  </main>
</body>
</html>
```